Morvane Business Card

We need a business card design for Morvane, an independent sewing pattern company based near Quebec City. We make patterns for children and adults and specialize in everything other big pattern brands won't tackle: activewear, sportswear (figure skating, gymnastics), underwear. We are a small business and would like our cards to be stylish and fun, not corporate looking.

Target Market(s)

Educated women 35-55 who sew for themselves or their family. They like fashion and sew to be different and make clothes that fit them like a glove, not necessarily to save money.

Industry/Entity Type

Small Business

Requirements
Must have
• Morvane logo, contact info:

Claire Dufresne, president & founder / présidente et fondatrice

Morvane
3156 rue Tessier
Ste-Odile QC H2K4P9
Canada

info@morvane.com
www.morvane.com
Nice to have
• Sewing/fashion-related graphics. You can use any pattern cover available on www.morvane.com for inspiration. Stylish illustrations / sketches inspired by existing garments we have would be great. Something showing pattern grading could also be an option.

The design can be on one- or two-sided. We are open to variations (e.g. 4-5 different backs for a given card)
Should not have
• nothing too cartoonish or girly please :) we prefer something timeless, fashion-forward.

```html
<!DOCTYPE html>
<html lang="en">
<head>
<meta charset="utf-8">
<title>Morvane Business Card</title>
<link rel="stylesheet" href="https://fonts.googleapis.com/css2?family=Open+Sans:wght@400;600;700&display=swap">
<style>
  :root {
    --page-bg: #d9d6d1;
    --card-white: #ffffff;
    --band-grey: #f0f0f2;
    --ink: #1c1c1c;
    --ink-soft: #2e2e2e;
    --card-black: #0b0b0b;
    --card-black-light: #262626;
    --ghost: #3a3a3c;
    --paper: #ffffff;
  }
  * { margin: 0; padding: 0; box-sizing: border-box; }
  html, body {
    width: 1200px; height: 1024px; overflow: hidden;
    background: var(--page-bg);
    font-family: "Open Sans", Arial, sans-serif;
  }
  .sheet {
    position: relative; width: 1200px; height: 1024px;
  }
  .card {
    position: absolute; left: 180px; width: 840px; height: 480px;
    border-radius: 38px; overflow: hidden;
    box-shadow: 0 10px 28px rgba(0,0,0,.22);
  }
  .card--front { top: 20px; background: var(--card-white); color: var(--ink); }
  .card--back {
    top: 524px;
    background: linear-gradient(125deg, var(--card-black-light) 0%, var(--card-black) 55%, #000 100%);
    color: var(--paper);
  }
  .front-band { position: absolute; inset: 0; }

  .wordmark { position: absolute; }
  .wordmark__name {
    display: block; font-weight: 700; line-height: 1; letter-spacing: -1px;
  }
  .wordmark__rule { display: block; height: 5px; margin-top: 8px; }
  .wordmark__tagline {
    display: block; text-align: right; font-weight: 600;
    font-size: 9px; letter-spacing: 1px; margin-top: 5px;
  }

  .card--front .wordmark { left: 60px; top: 178px; width: 250px; }
  .card--front .wordmark__name { font-size: 60px; color: var(--ink); }
  .card--front .wordmark__rule { background: var(--ink); }
  .card--front .wordmark__tagline { color: var(--ink); }

  .contact {
    position: absolute; left: 500px; top: 120px;
    list-style: none; font-size: 22px; line-height: 34px; color: var(--ink-soft);
  }
  .contact__item { display: flex; align-items: center; gap: 12px; }
  .contact__icon { width: 18px; height: 18px; flex: none; }
  .contact__item--plain { padding-left: 30px; }

  .person { position: absolute; left: 400px; top: 360px; }
  .person__name { font-size: 27px; font-weight: 700; color: var(--ink); }
  .person__role { font-size: 22px; color: var(--ink-soft); margin-top: 2px; }

  .ghost-mark {
    position: absolute; left: 40px; top: 120px;
    font-size: 190px; font-weight: 700; letter-spacing: -4px;
    color: var(--ghost); opacity: .55; line-height: 1;
  }
  .ghost-bar {
    position: absolute; left: 40px; top: 340px; width: 470px; height: 22px;
    background: var(--ghost); opacity: .55;
  }
  .card--back .wordmark { right: 60px; bottom: 110px; width: 300px; }
  .card--back .wordmark__name { font-size: 70px; color: var(--paper); }
  .card--back .wordmark__rule { background: var(--paper); height: 6px; }
  .card--back .wordmark__tagline { color: var(--paper); font-size: 11px; }
  .gloss {
    position: absolute; inset: 0;
    background: linear-gradient(115deg, rgba(255,255,255,.07) 0%, rgba(255,255,255,0) 45%);
  }
</style>
</head>
<body>
<main class="sheet">
  <section class="card card--front" aria-label="Card front">
    <svg class="front-band" viewBox="0 0 840 480" aria-hidden="true">
      <path d="M0 0 H840 V70 H390 C360 180 330 330 330 480 H210 C215 330 245 180 270 70 H0 Z" fill="var(--band-grey)"/>
    </svg>
    <div class="wordmark">
      <span class="wordmark__name">Morvane</span>
      <span class="wordmark__rule"></span>
      <span class="wordmark__tagline">PATRONS · PATTERNS</span>
    </div>
    <ul class="contact">
      <li class="contact__item">
        <svg class="contact__icon" viewBox="0 0 24 24" aria-hidden="true"><path d="M6.6 10.8a15 15 0 0 0 6.6 6.6l2.2-2.2a1 1 0 0 1 1-.25 11.4 11.4 0 0 0 3.6.6 1 1 0 0 1 1 1V20a1 1 0 0 1-1 1A17 17 0 0 1 3 4a1 1 0 0 1 1-1h3.5a1 1 0 0 1 1 1c0 1.25.2 2.45.6 3.6a1 1 0 0 1-.25 1z" fill="var(--ink)"/></svg>
        <span>418-555-0187</span>
      </li>
      <li class="contact__item">
        <svg class="contact__icon" viewBox="0 0 24 24" aria-hidden="true"><path d="M2 5h20v14H2z M2 5l10 8 10-8" fill="var(--ink)" stroke="var(--paper)" stroke-width="1.5"/></svg>
        <span>info@morvane.com</span>
      </li>
      <li class="contact__item">
        <svg class="contact__icon" viewBox="0 0 24 24" aria-hidden="true"><circle cx="12" cy="12" r="10" fill="var(--ink)"/><path d="M2 12h20M12 2c3 3 3 17 0 20M12 2c-3 3-3 17 0 20" stroke="var(--paper)" stroke-width="1.2" fill="none"/></svg>
        <span>www.morvane.com</span>
      </li>
      <li class="contact__item contact__item--plain">3156 rue Tessier</li>
      <li class="contact__item contact__item--plain">Ste-Odile QC H2K4P9</li>
    </ul>
    <div class="person">
      <p class="person__name">Claire Dufresne</p>
      <p class="person__role">president / présidente</p>
    </div>
  </section>

  <section class="card card--back" aria-label="Card back">
    <span class="ghost-mark" aria-hidden="true">Morvane</span>
    <span class="ghost-bar" aria-hidden="true"></span>
    <div class="gloss" aria-hidden="true"></div>
    <div class="wordmark">
      <span class="wordmark__name">Morvane</span>
      <span class="wordmark__rule"></span>
      <span class="wordmark__tagline">PATRONS · PATTERNS</span>
    </div>
  </section>
</main>
</body>
</html>
```